Home Security Company Business Card

Looking for a eye catching business card that is non traditional and stands out but yet still looks professional. It should include all the pertinent information such as name, title, address, telephone, e-mail, website address should definitely stand out and then finally the logo.

Target Market(s)

Residential and Commercial accounts mostly upscale accounts

Industry/Entity Type

Security

Contact Information for Business Card

Name
Title
Address
Office #
Cell #
E-mail
Website

Font styles to use
Serif
Sans Serif

Requirements
Must have
• Logo, two sided color configuration
Nice to have
• You decide
Should not have
• There really aren't any.

```html
<!DOCTYPE html>
<html lang="en">
<head>
<meta charset="utf-8">
<title>Bastion Guard Systems – Business Card</title>
<link rel="stylesheet" href="https://fonts.googleapis.com/css2?family=Source+Sans+3:wght@400;600&display=swap">
<style>
  :root {
    --stage-top: #2a2a2a;
    --stage-bottom: #050505;
    --card-white: #ffffff;
    --card-red: #7c1416;
    --maroon: #7a1517;
    --gold: #d9a53c;
    --cream: #f1ddb0;
  }
  html, body {
    margin: 0;
    padding: 0;
    width: 1200px;
    height: 900px;
    overflow: hidden;
  }
  body {
    background: linear-gradient(180deg, var(--stage-top) 0%, var(--stage-bottom) 100%);
    font-family: "Source Sans 3", "Myriad Pro", Arial, sans-serif;
    position: relative;
  }
  .card {
    position: absolute;
    top: 306px;
    width: 439px;
    height: 271px;
    border-radius: 12px;
    box-sizing: border-box;
  }
  .card--front { left: 149px; background: var(--card-white); }
  .card--back  { left: 608px; background: var(--card-red); }

  .brand {
    position: absolute;
    display: flex;
    align-items: center;
    font-weight: 600;
    line-height: 1.1;
    letter-spacing: 0.02em;
    text-transform: uppercase;
    white-space: nowrap;
  }
  .brand__mark {
    flex: none;
    border-radius: 50%;
  }
  .card--front .brand {
    left: 28px;
    top: 91px;
    gap: 9px;
    color: var(--maroon);
    font-size: 15px;
  }
  .card--front .brand__mark { width: 88px; height: 88px; background: var(--gold); }
  .card--back .brand {
    left: 86px;
    top: 74px;
    gap: 12px;
    color: var(--card-white);
    font-size: 20px;
  }
  .card--back .brand__mark { width: 122px; height: 122px; background: var(--cream); }

  .contact {
    position: absolute;
    left: 261px;
    top: 61px;
    color: var(--gold);
    font-size: 13px;
    line-height: 16px;
  }
  .contact__name {
    margin: 0;
    color: var(--maroon);
    font-weight: 600;
    font-size: 15.5px;
    line-height: 19px;
  }
  .contact__title { margin: 0 0 9px; }
  .contact__address { margin: 0 0 10px; font-style: normal; }
  .contact__list { list-style: none; margin: 0; padding: 0; }
  .contact__list li {
    display: flex;
    align-items: center;
    gap: 5px;
    height: 16px;
  }
  .contact__icon { width: 9px; height: 9px; fill: var(--maroon); flex: none; }
</style>
</head>
<body>
  <section class="card card--front" aria-label="Business card front">
    <div class="brand">
      <span class="brand__mark"></span>
      <span>Bastion Guard<br>Systems Inc.</span>
    </div>
    <div class="contact">
      <h1 class="contact__name">Daniel Reyes</h1>
      <p class="contact__title">Managing Director</p>
      <address class="contact__address">12345, Address Goes Here<br>Country Name, 123456.</address>
      <ul class="contact__list">
        <li>
          <svg class="contact__icon" viewBox="0 0 12 12" aria-label="Office phone"><path d="M1 4.2C1 2.6 3.4 1.6 6 1.6s5 1 5 2.6v.9H8.3V3.9H3.7v1.2H1z M2.6 6h6.8l1.3 4.6H1.3z M6 7a1.3 1.3 0 1 0 0 2.6A1.3 1.3 0 0 0 6 7z" fill-rule="evenodd"/></svg>
          044-123 456 789
        </li>
        <li>
          <svg class="contact__icon" viewBox="0 0 12 12" aria-label="Mobile"><path d="M3.2 0.5h5.6v11H3.2z M4.2 1.8v7.2h3.6V1.8z M5.4 9.6h1.2v1H5.4z" fill-rule="evenodd"/></svg>
          044-123 456 789
        </li>
        <li>
          <svg class="contact__icon" viewBox="0 0 12 12" aria-label="Email"><path d="M0.5 2.5h11v7h-11z M1.6 3.3L6 6.6l4.4-3.3z" fill-rule="evenodd"/></svg>
          info@webname.com
        </li>
        <li>
          <svg class="contact__icon" viewBox="0 0 12 12" aria-label="Website"><path d="M5.2 4.3L3.3 6.2a2 2 0 0 0 2.8 2.8l.8-.8-.8-.8-.8.8a.9.9 0 0 1-1.2-1.2L6 5.1z M6.8 7.7l1.9-1.9a2 2 0 0 0-2.8-2.8l-.8.8.8.8.8-.8a.9.9 0 0 1 1.2 1.2L6 6.9z M4.9 6.3l1.4-1.4.8.8-1.4 1.4z"/></svg>
          www.websitename.com
        </li>
      </ul>
    </div>
  </section>

  <section class="card card--back" aria-label="Business card back">
    <div class="brand">
      <span class="brand__mark"></span>
      <span>Bastion Guard<br>Systems Inc.</span>
    </div>
  </section>
</body>
</html>
```